High-end law practice specializing in closely held business succession planning and complex estates

Solo practitioner whose practice specializes in high-net worth, complex estate planning needs muliple versions of letterhead black and white, please. Letterhead should incorporate slogan, "Protecting your family business is my business," for one and "Complex Estate Planning"; third with no slogan. All for The Law Office of Marcy Lynn Pettibone, PC, 418 Cedar Hollow Ln., Newport News, Virginia 23648, Tel. 757-555-0142 Fax tbd email: marcy@mlplawgroup.example; Marcy Lynn Pettibone, Esq., principal, licensed in VA, NY, DC
Updates

Project Deadline Extended
Reason: My internet service went down and I can only view designs on my smart phone -- it's just too hard to review. So sorry! Working with my ISP now. Please be patient!

Target Market(s)

High net worth clients with complex estate planning needs, family businesses, family farmers, family foresters -- people with unique estate/succession planning needs who need a specialist who understands them.

Industry/Entity Type

Business

Font styles to use
Script

Requirements
Must have
• A high-end look and feel, connoting trustworthiness, special knowledge, and expertise.

```html
<!DOCTYPE html>
<html lang="en">
<head>
<meta charset="utf-8">
<title>The Law Office of Marcy Lynn Pettibone, PC — Letterhead</title>
<link rel="stylesheet" href="https://fonts.googleapis.com/css2?family=Noto+Serif:wght@400;500&display=swap">
<style>
  :root {
    --backdrop: #e9e6e1;
    --paper: #ffffff;
    --ink: #111111;
    --rule: #d6d6d6;
    --band: #000000;
  }
  * { margin: 0; padding: 0; box-sizing: border-box; }
  html, body {
    width: 953px;
    height: 1200px;
    overflow: hidden;
    background: var(--backdrop);
  }
  .letterhead {
    position: absolute;
    left: 139px;
    top: 150px;
    width: 676px;
    height: 955px;
    background: var(--paper);
    color: var(--ink);
    font-family: "Noto Serif", Georgia, serif;
    box-shadow: 0 2px 10px rgba(0,0,0,0.12);
  }
  .firm {
    position: absolute;
    left: 32px;
    top: 28px;
  }
  .firm-name {
    font-size: 20.5px;
    font-weight: 400;
    line-height: 25px;
    letter-spacing: 0.2px;
    text-transform: uppercase;
  }
  .firm-principal {
    font-size: 13px;
    line-height: 18px;
    margin-top: 1px;
  }
  .contact {
    position: absolute;
    left: 458px;
    top: 31px;
    padding-left: 8px;
    border-left: 1px solid var(--rule);
    font-size: 11.5px;
    line-height: 15px;
  }
  .contact-address { margin-bottom: 5px; }
  .slogan {
    position: absolute;
    left: 0;
    right: 0;
    top: 908px;
    text-align: center;
    font-size: 15.5px;
    letter-spacing: 0.6px;
  }
  .base-band {
    position: absolute;
    left: 0;
    bottom: 0;
    width: 100%;
    height: 9px;
    background: var(--band);
  }
</style>
</head>
<body>
  <main class="letterhead">
    <header>
      <div class="firm">
        <h1 class="firm-name">The Law Office<br>of Marcy Lynn Pettibone, PC</h1>
        <p class="firm-principal">Marcy Lynn Pettibone, Esq., licensed in VA, NY, DC</p>
      </div>
      <address class="contact" style="font-style: normal;">
        <p class="contact-address">418 Cedar Hollow Ln.,<br>Newport News, Virginia 23648</p>
        <p class="contact-lines">T: 757-555-0142 | F: 757-555-0199<br>E: marcy@mlplawgroup.example</p>
      </address>
    </header>
    <footer>
      <p class="slogan">Complex Estate Planning</p>
      <div class="base-band"></div>
    </footer>
  </main>
</body>
</html>
```